Copper Lantern

Need a business card for our restaurant. Restaurant and Bar in the mountains of North Idaho. Rustic looking card

rustic design, wood and metal looking, primarily neutral colors

• Name, address, phone number, website, email address

```html
<!DOCTYPE html>
<html lang="en">
<head>
<meta charset="utf-8">
<title>Copper Lantern — Business Card</title>
<link rel="stylesheet" href="https://fonts.googleapis.com/css2?family=Montserrat:wght@400;500;700&display=swap">
<style>
  :root {
    --backdrop: #3a3a3a;
    --card-dark: #141414;
    --card-dark-mark: #3c3c3c;
    --card-light: #ffffff;
    --ink: #111111;
    --ink-soft: #2b2b2b;
    --art-top: #1a1a1a;
    --art-bottom: #000000;
  }
  * { margin: 0; padding: 0; box-sizing: border-box; }
  html, body { width: 1200px; height: 875px; overflow: hidden; }
  body {
    background: var(--backdrop);
    font-family: "Montserrat", sans-serif;
    position: relative;
  }
  .card {
    position: absolute;
    top: 282px;
    width: 540px;
    height: 310px;
    border-radius: 18px;
    overflow: hidden;
  }
  .card--front { left: 40px; background: var(--card-dark); }
  .card--back { left: 620px; background: var(--card-light); color: var(--ink); }

  .mark-dot {
    flex: 0 0 auto;
    display: block;
    border-radius: 50%;
    border-style: solid;
    border-color: currentColor;
  }
  .front-mark {
    position: absolute;
    left: 50%; top: 50%;
    transform: translate(-50%, -50%);
    display: flex; align-items: center; gap: 14px;
    white-space: nowrap;
    color: var(--card-dark-mark);
  }
  .front-mark .mark-dot { width: 26px; height: 26px; border-width: 3px; }
  .front-mark .brand-name {
    font-size: 30px; font-weight: 500; letter-spacing: 2px; text-transform: uppercase;
    line-height: 1;
  }

  .back-brand {
    position: absolute; left: 30px; top: 34px;
    display: flex; align-items: center; gap: 10px;
    white-space: nowrap;
  }
  .back-brand .mark-dot { width: 20px; height: 20px; border-width: 2px; color: var(--ink); }
  .back-brand .brand-name {
    font-size: 17px; font-weight: 500; letter-spacing: 1.5px; text-transform: uppercase;
    line-height: 1;
  }

  .contact { position: absolute; left: 30px; top: 108px; white-space: nowrap; }
  .contact__name { font-size: 21px; font-weight: 700; line-height: 1.1; }
  .contact__role { font-size: 12px; font-weight: 400; color: var(--ink-soft); margin-bottom: 14px; }
  .contact__address { font-size: 12px; line-height: 1.35; margin-bottom: 10px; }
  .contact__list { list-style: none; font-size: 12px; }
  .contact__list li { display: flex; align-items: center; gap: 8px; line-height: 1.5; }
  .contact__list svg { width: 11px; height: 11px; fill: var(--ink); flex: 0 0 auto; }

  .brand-art {
    position: absolute; right: 40px; top: 28px;
    width: 200px; height: 254px; border-radius: 10px;
    background: linear-gradient(160deg, var(--art-top), var(--art-bottom));
  }
</style>
</head>
<body>
  <section class="card card--front">
    <div class="front-mark">
      <span class="mark-dot"></span>
      <span class="brand-name">Copper Lantern</span>
    </div>
  </section>

  <section class="card card--back">
    <div class="back-brand">
      <span class="mark-dot"></span>
      <span class="brand-name">Copper Lantern</span>
    </div>

    <div class="contact">
      <p class="contact__name">Mara Quinlan</p>
      <p class="contact__role">Managing Director</p>
      <p class="contact__address">48 Cedar Ridge Road,<br>Pine Hollow, USA</p>
      <ul class="contact__list">
        <li><svg viewBox="0 0 24 24"><path d="M6.6 10.8a15.1 15.1 0 0 0 6.6 6.6l2.2-2.2a1 1 0 0 1 1-.25 11.4 11.4 0 0 0 3.6.57 1 1 0 0 1 1 1V20a1 1 0 0 1-1 1A17 17 0 0 1 3 4a1 1 0 0 1 1-1h3.5a1 1 0 0 1 1 1c0 1.25.2 2.45.57 3.57a1 1 0 0 1-.25 1z"/></svg>(208) 555 0147</li>
        <li><svg viewBox="0 0 24 24"><path d="M2 5h20v14H2z M2 5l10 8 10-8" fill="none" stroke="#111" stroke-width="2"/></svg>hello@copperlantern.com</li>
        <li><svg viewBox="0 0 24 24"><circle cx="12" cy="12" r="10" fill="none" stroke="#111" stroke-width="2"/><path d="M2 12h20M12 2c3 3 3 17 0 20M12 2c-3 3-3 17 0 20" fill="none" stroke="#111" stroke-width="1.6"/></svg>www.copperlantern.com</li>
      </ul>
    </div>

    <div class="brand-art" role="img" aria-label="Large dark brand illustration area"></div>
  </section>
</body>
</html>
```